Business card por a urban DJ, up scale audience target

Need a sober design, modern, conservative colors but i can consider some options, y play rnb, hip hop, EDM and top40.

Business card for contact and personal info, double sided, use logo attrached please; im 42 so i need a card acording to my age an target audience.

Target Market(s)

Adult people, up scale audience

Industry/Entity Type

Music Download

Contact Information for Business Card

Cel (318) 4207265518 www.lumadrift.com

Requirements
Must have
• open mind
Nice to have
• open mind
Should not have
• DJ

```html
<!DOCTYPE html>
<html lang="en">
<head>
<meta charset="utf-8">
<title>Marco Vell — Business Card</title>
<link rel="stylesheet" href="https://fonts.googleapis.com/css2?family=Open+Sans:wght@400;700&display=swap">
<style>
  :root {
    --stage: #3a3a3a;
    --card: #050505;
    --ink-light: #c6c6c6;
    --ink-soft: #a9a9a9;
  }
  html, body {
    margin: 0;
    padding: 0;
    width: 1200px;
    height: 900px;
    overflow: hidden;
    background: var(--stage);
    font-family: "Open Sans", Arial, sans-serif;
  }
  .canvas {
    position: relative;
    width: 1200px;
    height: 900px;
  }
  .card {
    position: absolute;
    left: 290px;
    width: 620px;
    height: 354px;
    background: var(--card);
    overflow: hidden;
    box-shadow: 0 6px 18px rgba(0,0,0,0.45);
  }
  .card--front { top: 66px; }
  .card--back { top: 480px; }

  .wordmark {
    margin: 0;
    color: var(--ink-light);
    font-weight: 700;
    line-height: 1;
    letter-spacing: 2px;
  }
  .card--front .wordmark {
    position: absolute;
    left: 0;
    right: 0;
    top: 50%;
    transform: translateY(-50%);
    text-align: center;
    font-size: 118px;
  }
  .card--back .wordmark {
    position: absolute;
    left: 48px;
    top: 118px;
    font-size: 84px;
  }

  .contact {
    position: absolute;
    left: 350px;
    top: 62px;
    color: var(--ink-soft);
  }
  .contact__name {
    margin: 0;
    font-size: 21px;
    font-weight: 700;
    color: var(--ink-light);
    line-height: 1.15;
  }
  .contact__role {
    margin: 2px 0 8px;
    font-size: 11px;
    font-weight: 400;
    letter-spacing: 0.5px;
  }
  .contact__line {
    display: flex;
    align-items: center;
    gap: 7px;
    margin: 0 0 3px;
    font-size: 13px;
    font-weight: 400;
  }
  .contact__icon { width: 10px; height: 10px; flex: none; }

  .equalizer {
    position: absolute;
    left: 0;
    bottom: 0;
    width: 620px;
    height: 200px;
  }
  .equalizer rect { fill: var(--ink-light); }
</style>
</head>
<body>
<main class="canvas">

  <section class="card card--front" aria-label="Card front">
    <p class="wordmark">LUMA</p>
  </section>

  <section class="card card--back" aria-label="Card back">
    <p class="wordmark">LUMA</p>

    <div class="contact">
      <h1 class="contact__name">Marco Vell</h1>
      <p class="contact__role">CEO</p>
      <p class="contact__line">
        <svg class="contact__icon" viewBox="0 0 10 10" aria-hidden="true">
          <rect x="2.5" y="0.5" width="5" height="9" rx="1" fill="none" stroke="currentColor" stroke-width="1"/>
          <rect x="4.3" y="7.4" width="1.4" height="0.9" fill="currentColor"/>
        </svg>
        <span>(318) 4207265518</span>
      </p>
      <p class="contact__line">
        <svg class="contact__icon" viewBox="0 0 10 10" aria-hidden="true">
          <circle cx="5" cy="5" r="4.3" fill="none" stroke="currentColor" stroke-width="0.9"/>
          <ellipse cx="5" cy="5" rx="1.9" ry="4.3" fill="none" stroke="currentColor" stroke-width="0.8"/>
          <line x1="0.7" y1="5" x2="9.3" y2="5" stroke="currentColor" stroke-width="0.8"/>
        </svg>
        <span>www.lumadrift.com</span>
      </p>
    </div>

    <svg class="equalizer" viewBox="0 0 620 200" aria-hidden="true">
      <g>
        <rect x="4" y="145" width="9" height="55"/>
        <rect x="17" y="140" width="9" height="60"/>
        <rect x="30" y="150" width="9" height="50"/>
        <rect x="43" y="138" width="9" height="62"/>
        <rect x="56" y="155" width="9" height="45"/>
        <rect x="69" y="170" width="9" height="30"/><rect x="69" y="156" width="9" height="9"/>
        <rect x="82" y="145" width="9" height="55"/>
        <rect x="95" y="132" width="9" height="68"/>
        <rect x="108" y="152" width="9" height="48"/>
        <rect x="121" y="162" width="9" height="38"/>
        <rect x="134" y="172" width="9" height="28"/><rect x="134" y="158" width="9" height="9"/>
        <rect x="147" y="140" width="9" height="60"/>
        <rect x="160" y="130" width="9" height="70"/>
        <rect x="173" y="148" width="9" height="52"/>
        <rect x="186" y="160" width="9" height="40"/>
        <rect x="199" y="138" width="9" height="62"/>
        <rect x="212" y="152" width="9" height="48"/>
        <rect x="225" y="128" width="9" height="72"/>
        <rect x="238" y="115" width="9" height="85"/>
        <rect x="251" y="110" width="9" height="90"/>
        <rect x="264" y="125" width="9" height="75"/>
        <rect x="277" y="140" width="9" height="60"/>
        <rect x="290" y="118" width="9" height="82"/>
        <rect x="303" y="105" width="9" height="95"/>
        <rect x="316" y="112" width="9" height="88"/>
        <rect x="329" y="130" width="9" height="70"/>
        <rect x="342" y="108" width="9" height="92"/>
        <rect x="355" y="95" width="9" height="105"/>
        <rect x="368" y="104" width="9" height="96"/>
        <rect x="381" y="120" width="9" height="80"/>
        <rect x="394" y="100" width="9" height="100"/>
        <rect x="407" y="90" width="9" height="110"/>
        <rect x="420" y="110" width="9" height="90"/>
        <rect x="433" y="128" width="9" height="72"/>
        <rect x="446" y="140" width="9" height="60"/><rect x="446" y="126" width="9" height="9"/>
        <rect x="459" y="92" width="9" height="108"/>
        <rect x="472" y="75" width="9" height="125"/>
        <rect x="485" y="82" width="9" height="118"/>
        <rect x="498" y="70" width="9" height="130"/>
        <rect x="511" y="60" width="9" height="140"/>
        <rect x="524" y="80" width="9" height="120"/>
        <rect x="537" y="100" width="9" height="100"/><rect x="537" y="86" width="9" height="9"/>
        <rect x="550" y="50" width="9" height="150"/>
        <rect x="563" y="40" width="9" height="160"/>
        <rect x="576" y="60" width="9" height="140"/>
        <rect x="589" y="80" width="9" height="120"/><rect x="589" y="66" width="9" height="9"/>
        <rect x="602" y="25" width="9" height="175"/>
      </g>
    </svg>
  </section>

</main>
</body>
</html>
```